Rebrand & reskin fitbrisko.com (Uncoded)

Fitbrisko.com is a commerce website and app for sports and fitness classes and events. In order to improve its appeal, we invite designers to provide their 'skins' for the landing page, club page and event page. Designers can propose using alternate controls and layouts for these pages, and comment on ways to improve the site's usability. It must remain easy to use on a portrait mobile phone screen, responsive design where necessary to also provide a good experience on desktop.

Please navigate to fitbrisko.com and explore the site, and we look forwards to your suggestions!

Target Market(s)

Primary: Tech-savvy mobile users. Secondary: Desktop users

Industry/Entity Type

Health And Wellness

Number of Pages Required

3 page

Font styles to use
Sans Serif

Colors
ffffff
f37122

Requirements
Must have
• This brief is all about changing the look and feel of the site; the winning design will have an immediate 'wow' factor, yet not sacrifice the ease of finding and paying for classes. It must retain the logo, white and orange must be the primary colours used.
Should not have
• The colour palette must remain roughly as is; for example, a very dark site will not appeal.

```html
<!DOCTYPE html>
<html lang="en">
<head>
<meta charset="utf-8">
<title>Fitbrisko – Events</title>
<link href="https://fonts.googleapis.com/css2?family=Open+Sans:wght@400;600;700&display=swap" rel="stylesheet">
<style>
:root{
  --orange:#f37122;
  --orange-dim:#9c4a17;
  --orange-post:#c0561a;
  --white:#ffffff;
  --header:#979797;
  --page:#8f8f8f;
  --panel:#8c8c8c;
  --dark:#2a2a30;
  --dark-btn:#413a3c;
  --footer:#232323;
  --text:#4a4a4a;
  --nav-text:#2e2e2e;
}
*{box-sizing:border-box;margin:0;padding:0}
html,body{width:1200px;height:1049px;overflow:hidden}
body{font-family:"Open Sans",sans-serif;background:var(--page);position:relative;color:var(--text)}
.abs{position:absolute}
.site-header{left:0;top:0;width:1200px;height:102px;background:var(--header);border-bottom:1px solid #7d7d7d}
.brand{left:117px;top:36px;display:flex;align-items:center;gap:10px;font-size:27px;font-weight:700;color:#a9561f;letter-spacing:1px}
.brand-dot{width:26px;height:26px;border-radius:50%;background:#a9561f}
.main-nav{left:0;top:0;height:102px}
.nav-item{top:0;height:102px;display:flex;align-items:center;justify-content:center;font-size:16px;color:var(--nav-text);border-left:1px solid #868686}
.nav-item.active{background:linear-gradient(#333338,#1f1f22);color:#cfcfcf;border:none}
.sidebar{left:105px;top:102px;width:223px;height:879px;background:var(--dark)}
.side-item{left:0;width:223px;height:56px;display:flex;align-items:center;padding-left:68px;color:#9a9a9a;font-size:16.5px;border-bottom:1px solid #3c3c43}
.side-item svg{position:absolute;left:30px;top:16px}
.page-title{left:366px;top:141px;font-size:31px;color:#2f2f2f;letter-spacing:1px}
.event-panel{left:364px;top:206px;width:708px;height:775px;background:var(--panel);border-left:1px solid #999;border-right:1px solid #999}
.event-head{left:364px;top:206px;width:708px;height:42px;background:var(--orange-dim)}
.map{left:874px;top:277px;width:173px;height:182px;background:linear-gradient(135deg,#8b8880,#7f7b72);border:1px solid #777}
.avatar{left:399px;top:480px;width:52px;height:52px;border-radius:50%;background:linear-gradient(#6b5a4e,#3c342e)}
.member-name{left:459px;top:492px;font-size:17px;color:#494949}
.tab-box{left:394px;top:605px;width:655px;height:179px;border:1px solid #6d6d6d}
.tab{top:569px;height:37px;display:flex;align-items:center;justify-content:center;font-size:14.5px}
.tab.comment{left:394px;width:114px;border:1px solid #6d6d6d;border-bottom:none;color:#9c4a17;background:var(--panel)}
.tab.review{left:508px;width:105px;background:#2f2f35;color:#b4b4b4}
.comment-field{left:420px;top:619px;width:601px;height:102px;border:1px solid #7a7a7a;background:linear-gradient(#8d8d8d,#888);padding:12px 15px;font-size:13px;color:#4e4e4e}
.post-btn{left:420px;top:727px;width:97px;height:35px;background:var(--orange-post);color:#e8c8b5;display:flex;align-items:center;justify-content:center;font-size:15.5px}
.event-row{left:364px;width:708px;height:42px;background:linear-gradient(#3a3a40,#222227);color:#b9b9b9;font-size:16.5px;display:flex;align-items:center;padding-left:21px;border-bottom:1px solid #55555a}
.event-row svg{position:absolute;right:20px;top:15px}
.site-footer{left:0;top:981px;width:1200px;height:68px;background:var(--footer);color:#777;font-size:13.5px;text-align:center;padding-top:22px}
.login-modal{left:327px;top:213px;width:547px;height:252px;background:var(--white)}
.modal-title{left:0;width:547px;top:34px;text-align:center;font-size:30px;color:#333}
.modal-sub{left:0;width:547px;top:81px;text-align:center;font-size:14.5px;color:#666}
.field{top:117px;width:234px;height:39px;border:1px solid #cfcfcf;background:linear-gradient(#fff,#f1f1f1);font-size:13.5px;color:#999;padding:9px 17px}
.btn{top:174px;width:132px;height:39px;display:flex;align-items:center;justify-content:center;font-size:18px;color:#fff}
.btn.login{left:140px;background:var(--orange)}
.btn.signup{left:279px;background:var(--dark-btn)}
</style>
</head>
<body>
<header class="abs site-header">
  <div class="abs brand"><span class="brand-dot"></span>FITBRISKO</div>
  <nav class="abs main-nav">
    <div class="abs nav-item" style="left:428px;width:147px;border:none">CALENDAR</div>
    <div class="abs nav-item" style="left:575px;width:110px">FEED</div>
    <div class="abs nav-item" style="left:685px;width:142px">NEAR BY</div>
    <div class="abs nav-item" style="left:827px;width:139px">CLASSES</div>
    <div class="abs nav-item active" style="left:966px;width:115px">EVENT</div>
  </nav>
</header>

<aside class="abs sidebar">
  <div class="abs side-item" style="top:14px">
    <svg width="26" height="22" viewBox="0 0 26 22"><path d="M2 8h8V4l7 7-7 7v-4H2z" fill="#9a9a9a"/><path d="M15 2h8v18h-8" fill="none" stroke="#9a9a9a" stroke-width="2.5"/></svg>LOGIN</div>
  <div class="abs side-item" style="top:71px">
    <svg width="26" height="28" viewBox="0 0 26 28" style="top:13px"><rect x="3" y="2" width="20" height="24" rx="2" fill="none" stroke="#9a9a9a" stroke-width="2.5"/><path d="M13 12l1.5 3h3l-2.5 2 1 3-3-2-3 2 1-3-2.5-2h3z" fill="#9a9a9a"/></svg>MY DIARY</div>
  <div class="abs side-item" style="top:126px">
    <svg width="34" height="34" viewBox="0 0 34 34" style="left:26px;top:11px"><path d="M17 1l16 16-16 16L1 17z" fill="#9a9a9a"/><rect x="7" y="15" width="20" height="4" fill="#2a2a30"/><rect x="9" y="11" width="4" height="12" fill="#2a2a30"/><rect x="21" y="11" width="4" height="12" fill="#2a2a30"/></svg>MY CLUBS</div>
  <div class="abs side-item" style="top:182px;border:none">
    <svg width="24" height="26" viewBox="0 0 24 26" style="left:37px;top:13px"><circle cx="12" cy="7" r="6" fill="#9a9a9a"/><path d="M1 26v-6c0-4 4-6 11-6s11 2 11 6v6z" fill="#9a9a9a"/></svg>MY PROFILE</div>
</aside>

<h1 class="abs page-title" style="font-weight:400">EVENTS</h1>

<section class="abs event-panel"></section>
<div class="abs event-head"></div>
<div class="abs map" role="img" aria-label="Street map of the event location"></div>
<div class="abs avatar" role="img" aria-label="Member portrait"></div>
<div class="abs member-name">Dana Whitlow</div>

<div class="abs tab-box"></div>
<div class="abs tab comment">COMMENT</div>
<div class="abs tab review">REVIEW</div>
<div class="abs comment-field">Type your comment here</div>
<div class="abs post-btn">POST</div>

<div class="abs event-row" style="top:808px">EVENT TITTLE HERE<svg width="20" height="11" viewBox="0 0 20 11"><path d="M1 1l9 8 9-8" fill="none" stroke="#bbb" stroke-width="2"/></svg></div>
<div class="abs event-row" style="top:851px">EVENT TITTLE HERE<svg width="20" height="11" viewBox="0 0 20 11"><path d="M1 1l9 8 9-8" fill="none" stroke="#bbb" stroke-width="2"/></svg></div>
<div class="abs event-row" style="top:894px">EVENT TITTLE HERE<svg width="20" height="11" viewBox="0 0 20 11"><path d="M1 1l9 8 9-8" fill="none" stroke="#bbb" stroke-width="2"/></svg></div>

<footer class="abs site-footer">© 2016 Company Name &nbsp;All right reserved &nbsp;Term of Use</footer>

<div class="abs login-modal">
  <h2 class="abs modal-title" style="font-weight:400">Member Login</h2>
  <p class="abs modal-sub">Praesent elementum elit at tellus Curabitur metus ipsum</p>
  <div class="abs field" style="left:38px">Username</div>
  <div class="abs field" style="left:279px">Password</div>
  <div class="abs btn login">LOGIN</div>
  <div class="abs btn signup">SIGN UP</div>
</div>
</body>
</html>
```